Need to create logo for Harbourline Ventures Ltd

We supply the above mention products all around NZ. Trading under the company name Harbourline Ventures Ltd.

Industry/Entity Type

It Company

Contact Information for Business Card

Harbourline Ventures Ltd. 0800519203 0217043952 Brent@Talvora.co.nz contact Brent HOLM
Suppliers of Talvora Louvres, Aluminim Sable shutters, Fennroll curtains,Emberlyn outdoor heaters,Pyrovane outdoor heaters

```html
<!DOCTYPE html>
<html lang="en">
<head>
<meta charset="utf-8">
<title>Harbourline Ventures Ltd — Business Card</title>
<link rel="stylesheet" href="https://fonts.googleapis.com/css2?family=Jost:wght@400&family=Source+Sans+3:wght@400&display=swap">
<style>
  :root {
    --backdrop: #5a5a5a;
    --card-white: #ffffff;
    --brand-red: #c32027;
    --panel-black: #000000;
    --ink-dark: #3b3634;
    --text-light: #ffffff;
  }
  * { box-sizing: border-box; margin: 0; padding: 0; }
  html, body { width: 1200px; height: 900px; overflow: hidden; }
  body {
    position: relative;
    background: radial-gradient(ellipse at center, #5e5e5e 0%, var(--backdrop) 70%, #525252 100%);
    font-family: "Source Sans 3", "Myriad Pro", sans-serif;
  }
  .card { position: absolute; top: 170px; width: 346px; height: 561px; overflow: hidden; }
  .card-front { left: 259px; background: var(--card-white); }
  .card-back { left: 631px; background: var(--brand-red); }

  .name-banner {
    position: absolute; left: 11px; top: 9px; width: 324px; height: 67px;
    background: var(--brand-red); color: var(--text-light);
    font-family: "Jost", "Futura", sans-serif; font-size: 26px; letter-spacing: 0.5px;
    display: flex; align-items: center; justify-content: center;
  }
  .brand-mark {
    position: absolute; left: 133px; top: 140px; width: 80px; height: 80px;
    border-radius: 50%; background: var(--brand-red);
  }
  .company-name {
    position: absolute; left: 0; width: 346px; top: 256px; text-align: center;
    font-family: "Jost", "Futura", sans-serif; font-size: 19px; color: var(--ink-dark);
    letter-spacing: 0.2px; white-space: nowrap;
  }
  .contact-panel {
    position: absolute; left: 9px; top: 293px; width: 326px; height: 182px;
    background: var(--panel-black); padding: 30px 0 0 33px;
  }
  .contact-item {
    display: flex; align-items: center; height: 38px; color: var(--text-light); font-size: 16px;
  }
  .contact-icon {
    width: 28px; height: 28px; border-radius: 50%; background: var(--brand-red);
    border: 1.5px solid #d9d9d9; box-shadow: inset 0 0 0 2px var(--panel-black);
    display: flex; align-items: center; justify-content: center; margin-right: 7px;
  }
  .contact-icon svg { width: 13px; height: 13px; fill: var(--text-light); }
  .product-band {
    position: absolute; left: 9px; top: 478px; width: 326px; height: 69px;
    background: var(--brand-red); color: var(--text-light);
    font-size: 12.5px; line-height: 17px; text-align: center; padding-top: 9px;
    white-space: nowrap;
  }
  .back-frame {
    position: absolute; left: 29px; top: 26px; width: 288px; height: 502px;
    border: 1px solid rgba(255,255,255,0.9);
  }
  .back-mark {
    position: absolute; left: 103px; top: 160px; width: 140px; height: 140px;
    border-radius: 50%; background: rgba(255,255,255,0.2);
  }
</style>
</head>
<body>
  <section class="card card-front">
    <div class="name-banner">BRENT HOLM</div>
    <div class="brand-mark"></div>
    <div class="company-name">HARBOURLINE VENTURES LTD</div>
    <div class="contact-panel">
      <div class="contact-item">
        <span class="contact-icon"><svg viewBox="0 0 24 24"><path d="M6.6 10.8a15 15 0 0 0 6.6 6.6l2.2-2.2a1 1 0 0 1 1-.25 11.4 11.4 0 0 0 3.6.57 1 1 0 0 1 1 1V20a1 1 0 0 1-1 1A17 17 0 0 1 3 4a1 1 0 0 1 1-1h3.5a1 1 0 0 1 1 1c0 1.25.2 2.45.57 3.57a1 1 0 0 1-.25 1z"/></svg></span>
        0800519203
      </div>
      <div class="contact-item">
        <span class="contact-icon"><svg viewBox="0 0 24 24"><path d="M7 2h10a2 2 0 0 1 2 2v16a2 2 0 0 1-2 2H7a2 2 0 0 1-2-2V4a2 2 0 0 1 2-2zm0 4v11h10V6zm5 13a1 1 0 1 0 0 2 1 1 0 0 0 0-2z"/></svg></span>
        0217043952
      </div>
      <div class="contact-item">
        <span class="contact-icon"><svg viewBox="0 0 24 24"><path d="M2 5h20v2l-10 6L2 7zm0 4l10 6 10-6v10H2z"/></svg></span>
        Brent@Talvora.co.nz
      </div>
    </div>
    <div class="product-band">
      Suppliers of Talvora Louvres - Aluminim Sable shutters<br>
      Fennroll curtains - Emberlyn outdoor heaters<br>
      Pyrovane outdoor heaters
    </div>
  </section>

  <section class="card card-back">
    <div class="back-frame"></div>
    <div class="back-mark"></div>
  </section>
</body>
</html>
```